Bright Wave Labs

We need a professional letter head format for our company. Now we have a logo but need to desing a new logo also. I have uploaded our old logo. Use the color in the logo and design a new one.

Dear Designers , Need to mention "BWL" and please dont use our old LOGO. we need a new catchy one.

```html
<!DOCTYPE html>
<html lang="en">
<head>
<meta charset="utf-8">
<title>Bright Wave Labs — Letterhead</title>
<link href="https://fonts.googleapis.com/css2?family=Source+Sans+3:wght@400;600;700&family=Arimo:wght@700&display=swap" rel="stylesheet">
<style>
  :root {
    --paper: #ffffff;
    --ink: #2b2b2b;
    --navy: #0f2238;
    --green: #8cc03f;
    --rule: #1f3550;
  }
  * { margin: 0; padding: 0; box-sizing: border-box; }
  html, body { width: 1059px; height: 1200px; overflow: hidden; background: var(--paper); }
  .letterhead {
    position: relative;
    width: 1059px;
    height: 1200px;
    background: var(--paper);
    font-family: "Source Sans 3", sans-serif;
    color: var(--ink);
  }
  .brand {
    position: absolute;
    top: 44px;
    left: 0;
    width: 100%;
    display: flex;
    flex-direction: column;
    align-items: center;
    gap: 12px;
  }
  .brand-mark {
    width: 76px;
    height: 76px;
    border-radius: 50%;
    background: var(--green);
  }
  .brand-name {
    font-family: "Source Sans 3", sans-serif;
    font-weight: 700;
    font-size: 19px;
    line-height: 22px;
    letter-spacing: 0.4px;
    color: var(--navy);
  }
  .greeting {
    position: absolute;
    top: 243px;
    left: 89px;
    font-family: "Arimo", sans-serif;
    font-weight: 700;
    font-size: 22px;
    line-height: 26px;
    color: var(--navy);
  }
  .letter-body {
    position: absolute;
    top: 289px;
    left: 89px;
    width: 886px;
  }
  .letter-body p {
    font-size: 21.6px;
    line-height: 22.2px;
    text-align: justify;
    margin-bottom: 22.2px;
  }
  .sign-off {
    position: absolute;
    top: 800px;
    left: 84px;
    width: 190px;
    height: 66px;
  }
  .signature {
    position: absolute;
    top: 0;
    left: 0;
    width: 164px;
    height: 44px;
    background: linear-gradient(90deg, #e9e9e9, #f5f5f5);
  }
  .closing {
    position: absolute;
    top: 42px;
    left: 6px;
    font-weight: 600;
    font-size: 19px;
    line-height: 22px;
    color: #111;
    white-space: nowrap;
  }
  .footer {
    position: absolute;
    left: 0;
    top: 1140px;
    width: 100%;
    height: 60px;
  }
  .footer-rule {
    position: absolute;
    top: 6px;
    left: 160px;
    width: 740px;
    height: 2px;
    background: linear-gradient(90deg, rgba(31,53,80,0.3), var(--rule) 50%, rgba(31,53,80,0.3));
  }
  .footer-contacts {
    position: absolute;
    top: 17px;
    left: 0;
    width: 100%;
    display: flex;
    justify-content: center;
    align-items: center;
    gap: 24px;
    font-size: 16px;
    line-height: 20px;
    color: #111;
  }
  .contact-item { display: inline-flex; align-items: center; gap: 5px; }
  .contact-item svg { width: 13px; height: 13px; fill: var(--navy); }
  .footer-address {
    position: absolute;
    top: 39px;
    left: 0;
    width: 100%;
    text-align: center;
    font-size: 14.5px;
    line-height: 18px;
    color: #111;
  }
</style>
</head>
<body>
<main class="letterhead">
  <header class="brand">
    <div class="brand-mark"></div>
    <div class="brand-name">BRIGHT WAVE LABS</div>
  </header>

  <h1 class="greeting">Dear Mr. Carter,</h1>

  <section class="letter-body">
    <p>Lorem Ipsum is simply dummy text of the printing and typesetting industry. Lorem Ipsum has been the industry's standard dummy text ever since the 1500s, when an unknown printer took a galley of type and scrambled it to make a type specimen book. It has survived not only five centuries, but also the leap into electronic typesetting, remaining essentially unchanged.</p>
    <p>The standard chunk of Lorem Ipsum used since the 1500s is reproduced below for those interested. Sections 1.10.32 and 1.10.33 from "de Finibus Bonorum et Malorum" by Aulen Tessaro are also reproduced in their exact original form, accompanied by English versions from the 1914 translation by H. Morvelle</p>
    <p>Lorem Ipsum is simply dummy text of the printing and typesetting industry. Lorem Ipsum has been the industry's standard dummy text ever since the 1500s, when an unknown printer took a galley of type and scrambled it to make a type specimen book. It has survived not only five centuries, but also the leap into electronic typesetting, remaining essentially unchanged. It was popularised in the</p>
    <p>The standard chunk of Lorem Ipsum used since the 1500s is reproduced below for those interested. Sections 1.10.32 and 1.10.33 from "de Finibus Bonorum et Malorum" by Aulen Tessaro are also reproduced in their exact original form, accompanied by English versions from the 1914 translation by H. Morvelle</p>
  </section>

  <div class="sign-off">
    <div class="signature" role="img" aria-label="Handwritten signature of the sender"></div>
    <div class="closing">Valued customers,</div>
  </div>

  <footer class="footer">
    <div class="footer-rule"></div>
    <div class="footer-contacts">
      <span class="contact-item">
        <svg viewBox="0 0 24 24" aria-hidden="true"><path d="M6.6 10.8a15.1 15.1 0 0 0 6.6 6.6l2.2-2.2c.3-.3.7-.4 1-.2 1.1.4 2.3.6 3.6.6.6 0 1 .4 1 1V20c0 .6-.4 1-1 1A17 17 0 0 1 3 4c0-.6.4-1 1-1h3.5c.6 0 1 .4 1 1 0 1.3.2 2.5.6 3.6.1.3 0 .7-.2 1l-2.3 2.2z"/></svg>
        (+912)480-337-204
      </span>
      <span class="contact-item">
        <svg viewBox="0 0 24 24" aria-hidden="true"><path d="M2 6h20v12H2z M4 8v.3l8 5 8-5V8l-8 5z" fill-rule="evenodd"/></svg>
        info@brightwavelabs.com
      </span>
      <span class="contact-item">www.brightwavelabs.com</span>
    </div>
    <div class="footer-address">Po. box 418, Harbor Lane, Westfield, Zip Code - 00000</div>
  </footer>
</main>
</body>
</html>
```